New Joomla Website for Marquee Hire Co

We need a web design for our new Marquee Hire Co here in New Zealand called Breezy Canopies.
We rather like the retro look, as it fit very well with the current trends in weddings that is a more of a retro look (and we had our logo designed to reflect that!). The 50's and 60's wedding styles are really making a comeback. We would like to communicate to that market effectively.

The Home page should have a slider image with space for a headline on it. It is a visual product we have (but we are selling that dream of a perfect wedding/party/event).

Our competition here have a really nice site that you could look at - www.plovanto.co.nz

The other pages would have space for a picture, and then a blurb under each element related to it.
We will have a FAQ, Gallery, Hire and Contact us pages - we will add them as we go along.

From a technical perspective, we are using Joomla 2.5 and upwards.

Any questions - let me know. I look forward seeing the designs!

Target Market(s)

Couples looking for a wedding marquee, birthday parties, Corporate events

Industry/Entity Type

Wedding

Requirements
Must have
• 1. Preferably done in Joomla. I will also look at Wordpress site.
2. It has to have a retro look and feel.
3. It has to use my brand new logo (included)

```html
<!DOCTYPE html>
<html lang="en">
<head>
<meta charset="utf-8">
<title>Breezy Canopies – Marquee Hire New Zealand</title>
<link rel="stylesheet" href="https://fonts.googleapis.com/css2?family=Lobster&family=Josefin+Sans:wght@400;600&family=Oswald:wght@300&family=Tinos&display=swap">
<style>
:root{
  --paper:#f8f6f1;
  --white:#ffffff;
  --brown:#5b3b22;
  --brown-dark:#3f2814;
  --sky:#a9c4e2;
  --sky-deep:#5f94b0;
  --circle-blue:#b4cdeb;
  --circle-pink:#f1c9d2;
  --sand:#e2c08c;
  --text:#5a3a1e;
  --teal:#2d5f73;
}
*{margin:0;padding:0;box-sizing:border-box}
html,body{width:1200px;height:1120px;overflow:hidden}
body{background:var(--paper);position:relative;font-family:"Tinos",serif;color:var(--text)}
.top-band{position:absolute;left:0;top:0;width:1200px;height:226px;background:var(--white)}
.social{position:absolute;top:16px;left:1006px;display:flex;gap:5px}
.social span{width:24px;height:24px;border-radius:50%;background:var(--sand);display:block}
.brand{position:absolute;left:110px;top:92px;display:flex;align-items:center;gap:12px;z-index:3}
.brand-dot{width:40px;height:40px;border-radius:50%;background:var(--sky-deep)}
.brand-name{font-family:"Lobster",cursive;font-size:40px;color:var(--brown)}
.main-nav{position:absolute;left:532px;top:114px;display:flex;gap:38px;font-family:"Lobster",cursive;font-size:27px}
.main-nav a{color:var(--sky);text-decoration:none;text-shadow:1px 1px 0 #6f8aa6}
.main-nav a.active{color:var(--sand);text-shadow:1px 1px 0 #9a7a4d}
.nav-rule{position:absolute;left:530px;top:174px;width:559px;height:1px;background:#c9ad92}
.slider{position:absolute;left:109px;top:179px;width:980px;height:380px;overflow:hidden}
.slide-photo{position:absolute;inset:0;background:linear-gradient(180deg,#6f8a4a 0%,#dcdcd8 35%,#eeeeec 55%,#8a7868 85%,#6e5f52 100%)}
.slide-panel{position:absolute;left:666px;top:0;width:314px;height:380px;background:rgba(255,255,255,.72);text-align:center;white-space:nowrap}
.panel-line1{font-family:"Lobster",cursive;font-size:30px;line-height:36px;color:var(--brown);margin-top:30px}
.panel-line2{font-family:"Oswald",sans-serif;font-weight:300;font-size:29px;line-height:40px;color:var(--brown);margin-top:2px}
.panel-line3{font-family:"Josefin Sans",sans-serif;font-size:18px;line-height:24px;color:var(--brown);margin-top:2px}
.panel-star{font-size:18px;color:var(--teal);margin-top:16px}
.panel-cta{position:absolute;left:0;width:314px;top:282px;font-family:"Lobster",cursive;font-size:24px;line-height:.75;color:var(--teal)}
.slider-dots{position:absolute;left:18px;bottom:14px;display:flex;gap:10px}
.slider-dots span{width:21px;height:21px;border-radius:50%;background:rgba(255,255,255,.45);border:2px solid rgba(255,255,255,.6)}
.slider-dots span.on{background:var(--sand)}
.arrow{position:absolute;top:330px}
.arrow.prev{left:72px}.arrow.next{left:1108px}
.slider-rule{position:absolute;left:109px;width:980px;height:1px;background:var(--brown)}
.promo{position:absolute;top:614px;width:206px;height:206px;border-radius:50%;z-index:2;overflow:hidden}
.promo::after{content:"";position:absolute;inset:7px;border-radius:50%;border:1px dashed var(--brown-dark);z-index:2}
.promo.rates{left:232px;background:var(--circle-blue)}
.promo.offers{left:495px;background:var(--circle-blue);border:6px solid var(--sky-deep)}
.promo.hire{left:758px;background:var(--circle-pink)}
.promo-text{position:absolute;font-family:"Josefin Sans",sans-serif;font-size:15px;line-height:1.3;color:var(--brown)}
.rates .promo-text{top:62px;left:0;width:206px;text-align:center}
.rates .promo-art{position:absolute;left:18px;top:118px;width:170px;height:48px;background:linear-gradient(90deg,#8c7a6a,#5b3b22 50%,#8c7a6a)}
.offers .promo-label{position:absolute;top:26px;left:0;width:194px;text-align:center;font-family:"Josefin Sans",sans-serif;font-size:14px;color:var(--white);z-index:3}
.offers .promo-art{position:absolute;left:28px;top:50px;width:138px;height:150px;background:linear-gradient(90deg,#e4ddd0 0%,#c4b49c 45%,#6a4a30 55%,#4a3020 100%)}
.hire .promo-text{top:58px;right:24px;width:172px;text-align:right;font-size:14.5px;line-height:19.5px}
.hire .promo-cta{position:absolute;top:136px;left:0;width:206px;text-align:center;font-family:"Oswald",sans-serif;font-weight:300;font-size:34px;color:var(--brown);letter-spacing:1px}
.ribbon{position:absolute;left:80px;top:796px;z-index:1}
.info{position:absolute;top:884px;width:290px;font-size:16px;line-height:18px}
.info h2{font-family:"Lobster",cursive;font-weight:400;font-size:24px;line-height:30px;color:var(--sky);margin-bottom:8px;letter-spacing:-.5px}
.info.contact{left:130px}.info.about{left:457px;width:285px}.info.tweets{left:784px}
.info p + p{margin-top:18px}
.to-top{position:absolute;left:560px;top:1072px}
.copyright{position:absolute;left:798px;top:1090px;font-family:"Josefin Sans",sans-serif;font-size:12px;color:var(--sky-deep);letter-spacing:-.2px}
</style>
</head>
<body>
<div class="top-band"></div>

<div class="social"><span></span><span></span><span></span></div>

<div class="brand"><span class="brand-dot"></span><span class="brand-name">Breezy Canopies</span></div>

<nav class="main-nav">
  <a class="active" href="#">Home</a>
  <a href="#">Faq</a>
  <a href="#">Gallery</a>
  <a href="#">Hire</a>
  <a href="#">Contact Us</a>
</nav>
<div class="nav-rule"></div>

<svg class="arrow prev" width="20" height="58" viewBox="0 0 20 58"><polygon points="18,0 0,29 18,58" fill="#8fb3c9"/></svg>
<svg class="arrow next" width="20" height="58" viewBox="0 0 20 58"><polygon points="2,0 20,29 2,58" fill="#8fb3c9"/></svg>

<section class="slider">
  <div class="slide-photo" role="img" aria-label="Photo of guests mingling outside a large white stretch marquee at a garden wedding"></div>
  <div class="slide-panel">
    <p class="panel-line1">Contact us for a quote</p>
    <p class="panel-line2">YOU MIGHT BE PLEASANTLY</p>
    <p class="panel-line3">SURPRISED WITH OUR RATES!</p>
    <p class="panel-star">*</p>
    <p class="panel-cta">Get<br>a<br>Quote</p>
  </div>
  <div class="slider-dots"><span class="on"></span><span></span><span></span><span></span></div>
</section>
<div class="slider-rule" style="top:565px"></div>
<div class="slider-rule" style="top:569px"></div>

<div class="promo rates">
  <p class="promo-text">Check Our Rates<br>You might be surprised!</p>
  <div class="promo-art" role="img" aria-label="Retro illustration of a marquee tent with stripes"></div>
</div>

<div class="promo offers">
  <p class="promo-label">Offers and Promotions</p>
  <div class="promo-art" role="img" aria-label="Illustration of a retro bride and groom"></div>
</div>

<div class="promo hire">
  <p class="promo-text">Have you ever dreamed of getting married by the beach, the lake or in the mountains?</p>
  <p class="promo-cta">HIRE*US</p>
</div>

<svg class="ribbon" width="1036" height="56" viewBox="0 0 1036 56">
  <polygon points="0,42 12,8 27,8 27,36 67,36" fill="#4a2f1a"/>
  <polygon points="1036,42 1024,8 1009,8 1009,36 969,36" fill="#4a2f1a"/>
  <polygon points="27,0 1009,0 1009,36 532,36 518,54 504,36 27,36" fill="#5b3b22"/>
</svg>

<section class="info contact">
  <h2>Contact</h2>
  <p>27 Tarrow Lane,<br>Kauri Bay, New Zealand</p>
  <p>+64 21 555 0142<br>contact@breezycanopies.co.nz</p>
</section>
<section class="info about">
  <h2>About</h2>
  <p>We are a dedicated team working to take part in your dreamed event project. Breezy Canopies is helping people build memories. Special occasions is worth celebrating.</p>
</section>
<section class="info tweets">
  <h2>Recent Tweets</h2>
  <p>2 hours ago : @BreezyCanopies Thank you for your service, it was fabulous!</p>
  <p>A day ago : New discount in Markees!</p>
</section>

<svg class="to-top" width="80" height="48" viewBox="0 0 80 48">
  <polygon points="40,0 80,48 0,48" fill="#5b3b22"/>
  <text x="40" y="38" text-anchor="middle" font-family="Lobster, cursive" font-size="20" fill="#ffffff">Up</text>
</svg>

<p class="copyright">© 2013 Breezy Canopies All Rights Reserved</p>
</body>
</html>
```